Las Vegas Tour guide needs website of future for physical and selfguided assets

Neon Drifters is the parent site to my Las Vegas tour operation. Within this is a physical walking tour called Whispers and the Racket, the site traffic driver where I tell history with a paranormal twist. The legacy site can be seen at spookyroutewalks.com.
The Neon Drifters app has self guided tours called Desert Hop Trail/Whispers and The Racket Retold/Calloway Row Stroll. Rivano is a 3rd party tour company I have partnered with to sale self-guided tours with a scavenger hunt theme.
I like black and pink and pistachio green colors however am flexible in theme. Colors should follow Vegas 50-60s aesthetics. The “Greetings From Silver Gulch Marker” should not be considered as design inspiration. 95% of traffic is on mobile. Final design should be easy to understand guided versus self-guided option. Show cross promotion links for digital assets/physical tour. Rivano content tbd by end of week 9 Aug 2021
sites i like
nationalspiritstrolls.com
heronsandshades.com
oldportphantomtrips.net
Updates

Needs a book now at top, or floating like lorvantrips. Less busy and stay away from using photos. I have included more websites for inspiration. I would like a mashup of the two sites eerieechoplace and lorvantrips. I am unsure what some of your designs would look like on a mobile screen. Please screenshot that. https://eerieechoplace.com/ https://www.lorvantrips.com/ https://k7vrx.com/ https://bqspecters.com/ https://bluefinjaunts.com/tours/new-york-city/shades-of-pellham-corner/

Family member hospitalized need extra time to review

Target Market(s)

Tourist 25+

Industry/Entity Type

Travel. Tour guide.

Coding

Coded - Design and coding required

Number of Pages Required

5+ page

Font styles to use
Serif

Colors
00AB8E
00BBA5
67D7C9
C6EFE9
E9F9F6
59FF00
82FF00
B8FF75
E3FFCB
F4FFEA
EB3D1F
EC4F4E
F09395
F8D3D4
FCEDEE
E54698
E96AAD
F1A4CE
F9D9EA
FCEFF6

Requirements
Must have
• Cross promotion between physical tour and digital
Nice to have
• sliver button like ads as breaks between tour info
Should not have
• "Greetings from Silver Gulch Marker". no photos. no animation.

```html
<!DOCTYPE html>
<html lang="en">
<head>
<meta charset="utf-8">
<title>Calloway Row Stroll – Las Vegas Walking Tours</title>
<link href="https://fonts.googleapis.com/css2?family=Rajdhani:wght@500;600;700&family=Mulish:wght@400;600;700&display=swap" rel="stylesheet">
<style>
:root{
  --orange:#f7931e;
  --red:#eb3d1f;
  --teal:#00ab8e;
  --lime:#59ff00;
  --black:#000;
  --ink:#1a1a1a;
  --body:#555;
  --paper:#eeeeee;
  --white:#fff;
}
*{margin:0;padding:0;box-sizing:border-box}
html,body{width:1200px;height:3362px;overflow:hidden}
body{font-family:"Mulish",sans-serif;color:var(--ink);background:var(--paper);position:relative}
.head{font-family:"Rajdhani",sans-serif;font-weight:600}
.btn{display:inline-block;background:var(--orange);color:var(--white);font:600 15px "Mulish",sans-serif;padding:0 18px;line-height:40px;text-decoration:none;white-space:nowrap}
.btn-ghost{background:transparent;color:var(--orange);border:1px solid var(--orange);line-height:38px}
.divider{width:54px;height:2px;margin:14px auto 0;background:linear-gradient(90deg,var(--teal) 50%,var(--red) 50%)}
.section-title{font-family:"Rajdhani",sans-serif;font-weight:600;font-size:44px;color:var(--teal);text-align:center;line-height:1}
.brand{display:flex;align-items:center;justify-content:center;gap:12px;font:700 30px "Rajdhani",sans-serif;color:var(--orange)}
.brand-dot{width:46px;height:46px;border-radius:50%;background:var(--orange)}

/* hero */
.hero{position:absolute;left:0;top:0;width:1200px;height:671px;background:radial-gradient(ellipse at 50% 40%,#4a3a33 0%,#2a2424 55%,#151313 100%)}
.hero-photo{position:absolute;inset:0}
.nav{position:absolute;left:142px;top:20px;width:917px;height:39px;display:flex;align-items:center}
.nav a{color:var(--white);font:600 14px "Mulish",sans-serif;text-decoration:none;margin-right:58px}
.nav .btn{position:absolute;right:0;top:0;margin:0;line-height:39px;font-size:15px}
.hero-brand{position:absolute;left:0;width:1200px;top:300px}
.hero-brand .brand{font-size:40px}
.hero-brand .brand-dot{width:60px;height:60px}
.hero-line{position:absolute;left:0;width:1200px;text-align:center;font-size:42px;line-height:1}
.hero-line.one{top:414px;color:var(--red)}
.hero-line.two{top:468px}
.hero-line.two .g{color:var(--lime)}
.hero-line.two .t{color:var(--teal);margin-left:14px}
.hero .cta{position:absolute;left:551px;top:528px;line-height:36px}

/* featured */
.featured{position:absolute;top:671px;left:0;width:1200px;height:700px;background:var(--paper)}
.featured .section-title{margin-top:67px}
.cards{position:absolute;left:142px;top:143px;display:flex;gap:11px}
.card{width:298px;height:457px;background:#f6f6f6;border:1px solid #e4e4e4;text-align:center;position:relative}
.card-img{height:214px;position:relative}
.tag{position:absolute;right:0;top:14px;background:var(--lime);color:#111;font:600 13px "Mulish",sans-serif;padding:0 16px;line-height:30px}
.card h3{font:700 18px "Mulish",sans-serif;color:#111;margin-top:24px;line-height:1.1;padding:0 20px}
.card h3.two{margin-top:14px}
.card p{font-size:13px;color:var(--body);line-height:25px;padding:0 10px;margin-top:14px;max-height:100px;overflow:hidden}
.card .actions{position:absolute;left:0;right:0;top:401px;display:flex;justify-content:center;gap:15px}
.card .actions .btn{font-weight:600}

/* about */
.about{position:absolute;top:1371px;left:0;width:1200px;height:474px;background:var(--black);text-align:center}
.about .section-title{margin-top:100px;font-size:42px}
.about p{color:var(--white);font-size:14px;line-height:25px;width:830px;margin:20px auto 0}
.about p+p{margin-top:7px}
.about .btn{margin-top:35px;line-height:42px}

/* reviews */
.reviews{position:absolute;top:1845px;left:0;width:1200px;height:488px;background:var(--paper)}
.reviews .section-title{margin-top:100px}
.review{position:absolute;top:216px;width:284px;height:172px;background:var(--white);border-radius:0 0 22px 0;box-shadow:0 6px 14px rgba(0,0,0,.08);padding:18px 20px}
.stars{color:var(--orange);font-size:12px;letter-spacing:1px}
.quote{position:absolute;right:22px;top:-26px;font:700 90px/1 "Rajdhani",sans-serif;color:var(--orange)}
.review p{font-size:12.5px;line-height:21px;color:#555;margin-top:12px}
.review .who{position:absolute;left:20px;top:140px;font:600 13px "Mulish",sans-serif;color:#111}
.arrow{position:absolute;top:283px;width:36px;height:36px;border-radius:50%;display:flex;align-items:center;justify-content:center}
.arrow.prev{left:69px;background:var(--white);box-shadow:0 2px 6px rgba(0,0,0,.12)}
.arrow.next{left:1094px;background:var(--teal)}

/* press */
.press{position:absolute;top:2333px;left:0;width:1200px;height:380px;background:var(--black)}
.press .section-title{margin-top:107px}
.press-row{position:absolute;left:142px;top:222px;width:917px;display:flex;justify-content:space-between;align-items:center}
.press-row span{font:600 19px "Rajdhani",sans-serif;color:var(--white);text-align:center;line-height:1.05}

/* call */
.call{position:absolute;top:2713px;left:0;width:1200px;height:227px;background:var(--paper);text-align:center}
.call .l1{font:600 48px/1 "Rajdhani",sans-serif;color:var(--teal);margin-top:62px}
.call .l2{font:600 48px/1 "Rajdhani",sans-serif;color:var(--orange);margin-top:10px;display:flex;justify-content:center;align-items:center;gap:14px}

/* footer */
.footer{position:absolute;top:2940px;left:0;width:1200px;height:422px;background:var(--black)}
.contact-box{position:absolute;top:82px;width:212px;height:156px;border:1px solid #333;text-align:center;color:var(--white)}
.contact-box svg{margin-top:36px}
.contact-box .label{font-size:15px;margin-top:12px}
.contact-box .value{font-size:14px;margin-top:8px}
.contact-box.email .value{font-size:12.5px}
.footer-brand{position:absolute;left:0;width:1200px;top:130px}
.footer .book{position:absolute;left:543px;top:283px;width:113px;line-height:36px;border:1px solid #ddd;color:var(--white);text-align:center;font:600 16px "Mulish",sans-serif;text-decoration:none}
.footer-rule{position:absolute;left:142px;top:355px;width:917px;height:1px;background:#222}
.copy{position:absolute;left:142px;top:377px;color:#ccc;font-size:12.5px}
.copy b{color:var(--white);font-weight:600}
.social{position:absolute;left:893px;top:371px;display:flex;gap:14px}
.social span{width:30px;height:28px;background:#1b1b1b;border:1px solid #333}
</style>
</head>
<body>

<header class="hero">
  <div class="hero-photo" role="img" aria-label="Night street scene of downtown Las Vegas with vintage neon signs"></div>
  <nav class="nav">
    <a href="#">Whispers And The Racket Las Vegas Walking Tour</a>
    <a href="#">Desert Hop Trail</a>
    <a href="#">Neon Drifters</a>
    <a class="btn" href="#">Book Now</a>
  </nav>
  <div class="hero-brand"><div class="brand"><span class="brand-dot"></span>Calloway Row Stroll</div></div>
  <h1 class="hero-line one head">Whispers &amp; The Racket Las Vegas Walking Tour</h1>
  <p class="hero-line two head"><span class="g">Desert Hop Trail</span><span class="t">Neon Drifters</span></p>
  <a class="btn cta" href="#">Book Now</a>
</header>

<section class="featured">
  <h2 class="section-title">Featured Tours</h2>
  <div class="divider"></div>
  <div class="cards">
    <article class="card">
      <div class="card-img" role="img" aria-label="Shadowy figure behind a lit doorway" style="background:linear-gradient(180deg,#3b2f2c,#8a7066 55%,#2a2220)"><span class="tag">45 Minute Walking Tour</span></div>
      <h3 class="two">Whispers &amp; The Racket Las Vegas Walking Tour</h3>
      <div class="divider"></div>
      <p>Lorem ipsum dolor sit amet, consectetuer adipiscing elit, sed diam nonummy nibh euismod tincidunt ut laoreet.</p>
      <div class="actions"><a class="btn" href="#">Book Now</a><a class="btn btn-ghost" href="#">Know More</a></div>
    </article>
    <article class="card">
      <div class="card-img" role="img" aria-label="Row of craft beer tasting glasses" style="background:linear-gradient(180deg,#3a1a0c,#b5621c 50%,#5a2a10)"><span class="tag">Self Guided Tours</span></div>
      <h3>Desert Hop Trail</h3>
      <div class="divider"></div>
      <p>Lorem ipsum dolor sit amet, consectetuer adipiscing elit, sed diam nonummy nibh euismod tincidunt ut laoreet dolore mgna aliquam erat volutpat.</p>
      <div class="actions"><a class="btn" href="#">Book Now</a><a class="btn btn-ghost" href="#">Know More</a></div>
    </article>
    <article class="card">
      <div class="card-img" role="img" aria-label="City roadside sign at night with glowing skyline" style="background:linear-gradient(180deg,#1b3a8a,#c05a2a 65%,#3a1a10)"><span class="tag">Lorem Ispum Dummy</span></div>
      <h3>Neon Drifters</h3>
      <div class="divider"></div>
      <p>Lorem ipsum dolor sit amet, consectetuer adipiscing elit, sed diam nonummy nibh euismod tincidunt ut laoreet dolore mgna aliquam erat volutpat.</p>
      <div class="actions"><a class="btn" href="#">Book Now</a><a class="btn btn-ghost" href="#">Know More</a></div>
    </article>
  </div>
</section>

<section class="about">
  <h2 class="section-title">About Calloway Row Stroll Walking Tour</h2>
  <div class="divider"></div>
  <p>Lorem ipsum dolor sit amet, consectetuer adipiscing elit, sed diam nonummy nibh euismod tincidunt ut laoreet dolore magna aliquam erat volutpat. Ut wisi enim ad minim veniam, quis nostrud exerci tation ullamcorper suscipit lobortis nisl ut aliquip ex ea commodo consequat. Duis autem vel eum iriure dolor in hendrerit in vulputate velit esse.</p>
  <p>Lorem ipsum dolor sit amet, consectetuer adipiscing elit, sed diam nonummy nibh euismod tincidunt ut laoreet dolore magna aliquam erat volutpat. Ut wisi enim ad minim veniam, quis nostrud exerci tation.</p>
  <a class="btn" href="#">Contact Us Today</a>
</section>

<section class="reviews">
  <h2 class="section-title">Customer Reviews</h2>
  <div class="divider"></div>
  <div class="arrow prev"><svg width="12" height="12" viewBox="0 0 12 12"><path d="M8 1 3 6l5 5" fill="none" stroke="#222" stroke-width="2"/></svg></div>
  <article class="review" style="left:142px"><div class="stars">★★★★★</div><span class="quote">”</span><p>“Lorem ipsum dolor sit amet, consectetur ipsum dolor sit amet, consectetur lodr adipiscing elit. Sed vel alique ellentesque justo. Mauris est tortor.”</p><div class="who">Nora Kessler</div></article>
  <article class="review" style="left:458px"><div class="stars">★★★★★</div><span class="quote">”</span><p>“Lorem ipsum dolor sit amet, consectetur ipsum dolor sit amet, consectetur lodr adipiscing elit. Sed vel alique ellentesque justo. Mauris est tortor.”</p><div class="who">Liam AM</div></article>
  <article class="review" style="left:776px"><div class="stars">★★★★★</div><span class="quote">”</span><p>“Lorem ipsum dolor sit amet, consectetur ipsum dolor sit amet, consectetur lodr adipiscing elit. Sed vel alique ellentesque justo. Mauris est tortor.”</p><div class="who">William WM</div></article>
  <div class="arrow next"><svg width="12" height="12" viewBox="0 0 12 12"><path d="m4 1 5 5-5 5" fill="none" stroke="#fff" stroke-width="2"/></svg></div>
</section>

<section class="press">
  <h2 class="section-title">As Seen On</h2>
  <div class="divider"></div>
  <div class="press-row">
    <span>Wander<br>Channel</span>
    <span>Gentleman<br>Monthly</span>
    <span>The Daily<br>Ledger</span>
    <span>BRN</span>
    <span>Young<br>Explorers</span>
    <span>Public<br>Radio Net</span>
  </div>
</section>

<section class="call">
  <p class="l1">Buy Tickets Online Or</p>
  <p class="l2">Give Us A Call At
    <svg width="40" height="40" viewBox="0 0 24 24" fill="none" stroke="#f7931e" stroke-width="1.4"><path d="M5 3h4l2 5-2.5 1.5a11 11 0 0 0 6 6L16 13l5 2v4a2 2 0 0 1-2 2A17 17 0 0 1 3 5a2 2 0 0 1 2-2z"/><path d="M15 3a6 6 0 0 1 6 6M15 6.5A2.5 2.5 0 0 1 17.5 9"/></svg>
    1-800-555-0142</p>
</section>

<footer class="footer">
  <div class="contact-box" style="left:142px">
    <svg width="40" height="40" viewBox="0 0 24 24" fill="none" stroke="#f7931e" stroke-width="1.4"><path d="M5 3h4l2 5-2.5 1.5a11 11 0 0 0 6 6L16 13l5 2v4a2 2 0 0 1-2 2A17 17 0 0 1 3 5a2 2 0 0 1 2-2z"/><path d="M15 3a6 6 0 0 1 6 6M15 6.5A2.5 2.5 0 0 1 17.5 9"/></svg>
    <div class="label">Phone</div><div class="value">555.018.2240</div>
  </div>
  <div class="footer-brand"><div class="brand"><span class="brand-dot"></span>Calloway Row Stroll</div></div>
  <a class="book" href="#">Book Now</a>
  <div class="contact-box email" style="left:846px">
    <svg width="44" height="40" viewBox="0 0 26 24" fill="none" stroke="#f7931e" stroke-width="1.4"><path d="M2 10l11-7 11 7v12H2z"/><path d="M2 10l11 7 11-7"/><path d="M6 12V6h14v6"/><path d="M9 9h8M9 11.5h6"/></svg>
    <div class="label">Email</div><div class="value">inquiry@callowayrow.com</div>
  </div>
  <div class="footer-rule"></div>
  <p class="copy">© 2021 <b>Calloway Row Walking Tour.</b> All Rights Reserved.</p>
  <div class="social" aria-label="Social links"><span></span><span></span><span></span><span></span></div>
</footer>

</body>
</html>
```